Plakate für ein Fest
Zielgruppe
Das Kessner Park ist ein Gewerbepark mit unterschiedlichen Mietern von Handwerker über Musiker bis hin zu Vermögensberatung. Wir veranstalten ein Fest für unsere Mieter und möchten dieses Plakat als Einladung nutzen.
Aufgabenstellung
Hintergrund schwarz, Logo verwenden
Get together
BBQ & Cocktails im Kessner Park
am 13.10.2023 ab 18 Uhr
Logo Band wild pebbles
Kinderbereich
Wir freuen uns darauf, alle Mieter mit Familien begrüßen zu dürfen! Auch an die Kleinen haben wir gedacht.

```html
<!DOCTYPE html>
<html lang="de">
<head>
<meta charset="utf-8">
<title>Get Together – BBQ &amp; Cocktails</title>
<link rel="stylesheet" href="https://fonts.googleapis.com/css2?family=Anton&family=Archivo:wght@700&family=Be+Vietnam+Pro:wght@600&display=swap">
<style>
  :root {
    --page: #e8e9eb;
    --ink: #141414;
    --paper: #2b2b2b;
    --white: #ffffff;
    --gold: #eccb87;
    --green: #3aac59;
  }
  html, body {
    margin: 0;
    width: 1000px;
    height: 1200px;
    overflow: hidden;
    background: var(--page);
  }
  .poster {
    position: absolute;
    left: 76px;
    top: 0;
    width: 848px;
    height: 1200px;
    background: var(--paper);
    overflow: hidden;
    color: var(--white);
  }
  .poster__photo {
    position: absolute;
    inset: 0;
    background:
      radial-gradient(ellipse at 30% 85%, rgba(120,120,120,.55), transparent 45%),
      radial-gradient(ellipse at 85% 40%, rgba(110,110,110,.5), transparent 50%),
      radial-gradient(ellipse at 40% 35%, rgba(80,80,80,.6), transparent 55%),
      linear-gradient(180deg, #2e2e2e 0%, #4a4a4a 55%, #2a2a2a 100%);
  }
  .poster > *:not(.poster__photo) { position: absolute; margin: 0; }
  .date {
    left: 35px;
    top: 52px;
    font-family: "Anton", sans-serif;
    line-height: 1;
  }
  .date__weekday { display: block; font-size: 66px; }
  .date__day { display: block; font-size: 158px; margin-top: 4px; line-height: 1; }
  .date__month { display: block; font-size: 64px; margin-top: 2px; }
  .brand {
    left: 470px;
    top: 66px;
    display: flex;
    align-items: center;
    gap: 18px;
  }
  .brand__mark { width: 40px; height: 40px; background: var(--green); }
  .brand__name {
    font-family: "Archivo", sans-serif;
    font-weight: 700;
    font-size: 52px;
    line-height: 0.98;
    letter-spacing: 1px;
    text-transform: uppercase;
  }
  .headline {
    left: 317px;
    top: 232px;
    font-family: "Anton", sans-serif;
    font-size: 88px;
    line-height: 1;
    white-space: nowrap;
  }
  .headline__accent { color: var(--gold); }
  .banner { left: 89px; top: 396px; width: 701px; height: 136px; }
  .banner__title {
    left: 166px;
    top: 398px;
    font-family: "Anton", sans-serif;
    font-size: 106px;
    line-height: 1.2;
    color: var(--ink);
    white-space: nowrap;
  }
  .when {
    left: 168px;
    top: 560px;
    font-family: "Anton", sans-serif;
    font-size: 56px;
    line-height: 1.2;
    color: var(--gold);
    white-space: nowrap;
  }
  .invite {
    left: 168px;
    top: 648px;
    width: 560px;
    font-family: "Be Vietnam Pro", sans-serif;
    font-weight: 600;
    font-size: 27px;
    line-height: 52px;
    letter-spacing: -0.5px;
  }
  .band {
    left: 320px;
    top: 898px;
    font-family: "Be Vietnam Pro", sans-serif;
    font-weight: 600;
    font-size: 40px;
    letter-spacing: 1px;
    line-height: 1.2;
  }
  .kids {
    left: 69px;
    top: 1036px;
    font-family: "Be Vietnam Pro", sans-serif;
    font-weight: 600;
    font-size: 50px;
    letter-spacing: -3px;
    line-height: 1.2;
    text-transform: uppercase;
  }
</style>
</head>
<body>
  <main class="poster">
    <div class="poster__photo" role="img" aria-label="Abgedunkeltes Schwarzweißfoto: Menschen feiern zusammen beim Grillen"></div>

    <h2 class="date">
      <span class="date__weekday">FREITAG</span>
      <span class="date__day">13</span>
      <span class="date__month">OKTOBER</span>
    </h2>

    <div class="brand">
      <span class="brand__mark"></span>
      <span class="brand__name">Kessner<br>Park</span>
    </div>

    <h1 class="headline"><span class="headline__accent">GET</span> TOGETHER</h1>

    <svg class="banner" viewBox="0 0 701 136" aria-hidden="true">
      <polygon points="77,0 701,0 621,136 0,136" fill="var(--gold)"/>
    </svg>
    <p class="banner__title">BBQ &amp; COCKTAILS</p>

    <p class="when">Ab 18.00 Uhr, Kessner Park</p>

    <p class="invite">Wir freuen uns darauf, alle Mieter mit Familien begrüßen zu dürfen! Auch an die Kleinen haben wir gedacht.</p>

    <p class="band">wild pebbles</p>

    <p class="kids">Mit Kinderbereich</p>
  </main>
</body>
</html>
```